Web Site Design for a Finance (lending) Company

We are opening a new subsidiary that focuses on lending money in the real estate industry. We need a web site designed to represent the business.

The business is lending money to real estate investors. A typical client/borrower will be looking to borrow money to buy a house, renovate it and then sell it at a profit, all within 12 months or less.

Company name is RTV Finance. Our logo is attached.

Attached is a general outline for the web site. We're working on writing more text for each page but this should give you enough to get started with some ideas.

Competitor web site that I like a lot (as an example): https://dorvaleqcapital.example/. Many of the general items on this site match what we will need (description of loan programs, FAQ)

Target Market(s)

Real estate investors (generally individuals or small companies with just a few people) who are buying homes, renovating them and then selling them at a profit.

Industry/Entity Type

Finance

Coding

Coded - Design and coding required

Number of Pages Required

5+ page

Colors

Designer to choose colors to be used in the design.

Requirements
Must have
• Minimalist design. Clean lines without too much clutter. Some stock photography is ok but the photos should not be distracting. They should almost fade in to the background so that user can focus on the key information about what our company does instead. We are a finance company, not a design company, so the information about our products will be more interesting to site visitors than the art.
• Some minimalist examples from Snapboard:
• https://www.snapboardia.example/explore/minimalist-web-design/
Nice to have
• If you search in zoovle for "hard money lenders" you will find many examples of web sites from our competition. I have provided a link above to competitor web site that I like a lot.
• I have attached our logo in EPS format. Logo is green. Web site doesn't have to be green but it should be of a color that will work well with the logo.

```html
<!DOCTYPE html>
<html lang="en">
<head>
<meta charset="utf-8">
<title>RTV Finance</title>
<link rel="stylesheet" href="https://fonts.googleapis.com/css2?family=Lato:wght@400;700&display=swap">
<style>
:root{
  --green:#0b4d2c;
  --green-soft:#17613b;
  --ink:#333;
  --text:#555;
  --muted:#777;
  --grey-band:#ebebeb;
  --line:#d0d0d0;
  --white:#fff;
}
*{margin:0;padding:0;box-sizing:border-box}
html,body{width:1200px;height:2731px;overflow:hidden;background:var(--white)}
body{position:relative;font-family:'Lato',sans-serif;color:var(--text)}
.abs{position:absolute}

/* header */
.topbar-phone{left:80px;top:44px;font-size:22px;color:var(--ink);display:flex;align-items:center;gap:14px}
.brand{left:0;width:1200px;top:34px;display:flex;justify-content:center;align-items:center;gap:14px}
.brand-mark{width:26px;height:26px;background:var(--green)}
.brand-name{font-size:38px;font-weight:700;color:var(--green)}
.chat-btn{left:923px;top:40px;width:199px;height:42px;background:var(--green);color:var(--white);font-size:20px;display:flex;align-items:center;justify-content:center}
.main-nav{left:0;top:126px;width:1200px;height:62px;background:var(--green);display:flex;justify-content:center;align-items:center;gap:52px}
.main-nav a{color:var(--white);text-decoration:none;font-size:19px;letter-spacing:.3px}

/* hero */
.hero-photo{left:0;top:188px;width:1200px;height:632px;background:linear-gradient(120deg,#3a3a3a 0%,#8b8b8b 35%,#d9d6d2 55%,#b9b3ab 75%,#6d6a66 100%)}
.hero-frame{left:246px;top:306px;width:706px;height:353px;border:3px solid var(--white)}
.hero-frame-accent{left:243px;top:452px;width:712px;height:210px;border:4px solid var(--green);border-top:none}
.hero-panel{left:273px;top:346px;width:647px;height:282px;background:rgba(220,220,220,.78);display:flex;align-items:center;justify-content:center;text-align:center}
.hero-panel h1{font-size:51px;font-weight:400;line-height:58px;color:#2b2b2b}
.hero-curve{left:0;top:730px}
.hero-dots{left:560px;top:790px;display:flex;gap:18px;align-items:center}
.dot{width:8px;height:8px;border-radius:50%;background:#555}
.dot.active{width:14px;height:14px;border:2px solid #555;background:none;position:relative}
.dot.active::after{content:"";position:absolute;left:3px;top:3px;width:4px;height:4px;border-radius:50%;background:#555}

/* section titles */
.section-title{left:0;width:1200px;text-align:center;font-size:44px;font-weight:400;color:var(--green)}
.section-title .soft{color:#555}

/* about */
.about-copy{left:190px;top:938px;width:820px;text-align:center;font-size:15px;line-height:25px;color:var(--text)}
.btn{height:51px;width:206px;background:var(--green);color:var(--white);font-size:21px;display:flex;align-items:center;justify-content:center;box-shadow:0 3px 0 #06341d}

/* loans */
.loans-band{left:0;top:1127px;width:1200px;height:417px;background:var(--grey-band)}
.loans-photo{left:0;top:1165px;width:565px;height:346px;background:radial-gradient(ellipse at 55% 40%,#c8c9b4 0%,#b6b39a 35%,#d9c3ae 60%,var(--grey-band) 85%)}
.loans-title{left:637px;top:1160px;font-size:44px;font-weight:400;color:var(--green)}
.loans-title .soft{color:#555}
.loan{left:640px;width:460px}
.loan-mark{position:absolute;left:0;top:12px;width:26px;height:4px;background:var(--green)}
.loan h3{margin-left:34px;font-size:28px;font-weight:400;color:#444;line-height:32px}
.loan p{margin-left:37px;font-size:14px;line-height:25px;color:var(--text)}
.loan .more{color:var(--green);font-weight:700}

/* team */
.team-card{top:1652px;width:250px;height:289px;border:2px solid #dedede;background:var(--white)}
.team-card.active{background:#efefef;border:3px solid var(--green);box-shadow:0 2px 4px rgba(0,0,0,.25)}
.team-photo{position:absolute;left:42px;top:34px;width:164px;height:166px;background:linear-gradient(180deg,#d8d4ce 0%,#b9aea2 45%,#3a4556 100%)}
.team-name{position:absolute;left:13px;top:199px;width:222px;height:51px;border:2px solid #c9c9c9;background:var(--white);display:flex;align-items:center;justify-content:center;font-size:21px;color:#555}

/* blog */
.blog-band{left:0;top:2001px;width:1200px;height:406px;background:var(--grey-band)}
.blog-card{top:2100px;width:310px;height:258px}
.blog-img{position:absolute;left:0;top:0;width:310px;height:187px}
.blog-date{position:absolute;left:0;top:3px;width:62px;height:69px;background:rgba(240,240,240,.95);text-align:center;color:#333}
.blog-date b{display:block;font-size:31px;font-weight:400;line-height:40px}
.blog-date span{font-size:13px}
.blog-text{position:absolute;left:11px;top:163px;width:288px;height:95px;background:var(--white);padding:12px 15px;box-shadow:0 3px 5px rgba(0,0,0,.2)}
.blog-text h4{font-size:14px;color:var(--green);font-weight:700;margin-bottom:8px}
.blog-text p{font-size:14px;line-height:25px;color:var(--text)}

/* footer */
.footer-heading{top:2448px;font-size:26px;font-weight:400;color:var(--green)}
.contact-row{left:78px;display:flex;gap:16px;font-size:15px;line-height:24px;color:var(--text)}
.contact-row svg{flex:none;margin-top:3px}
.news-item{left:433px;width:330px;display:flex;gap:12px}
.avatar{flex:none;width:55px;height:55px;border-radius:50%;background:linear-gradient(160deg,#d7c2b0,#6b7a90)}
.news-item p{font-size:15px;line-height:24px;color:var(--text)}
.news-item a{display:block;color:var(--green);font-weight:700;font-size:15px;text-decoration:none;line-height:18px}
.newsletter-copy{left:791px;top:2488px;width:310px;font-size:15px;line-height:24px;color:var(--text)}
.subscribe{left:789px;top:2586px;width:322px;height:47px;border:2px solid #bbb;border-radius:24px;display:flex;align-items:center;justify-content:space-between;padding-left:12px;font-size:15px;color:#666}
.subscribe-btn{width:76px;height:47px;margin-right:-2px;border-radius:24px;background:var(--green);display:flex;align-items:center;justify-content:center}
.copyright{left:0;top:2677px;width:1200px;height:54px;background:var(--green);color:var(--white);font-size:16px;display:flex;align-items:center;justify-content:center}
</style>
</head>
<body>

<header>
  <div class="abs topbar-phone">
    <svg width="20" height="20" viewBox="0 0 24 24"><path fill="#0b4d2c" d="M6.6 10.8a15.1 15.1 0 0 0 6.6 6.6l2.2-2.2c.3-.3.7-.4 1-.2 1.1.4 2.3.6 3.6.6.6 0 1 .4 1 1V20c0 .6-.4 1-1 1A17 17 0 0 1 3 4c0-.6.4-1 1-1h3.5c.6 0 1 .4 1 1 0 1.3.2 2.5.6 3.6.1.3 0 .7-.2 1z"/></svg>
    123 456 7890
  </div>
  <div class="abs brand"><span class="brand-mark"></span><span class="brand-name">RTV Finance</span></div>
  <div class="abs chat-btn">Chat with us!</div>
  <nav class="abs main-nav">
    <a href="#">HOME</a><a href="#">ABOUT US</a><a href="#">LOANS</a><a href="#">RESOURCES</a><a href="#">CONTACT US</a>
  </nav>
</header>

<section class="hero">
  <div class="abs hero-photo" role="img" aria-label="Photo of hands signing a document beside a small model house"></div>
  <div class="abs hero-frame"></div>
  <div class="abs hero-frame-accent"></div>
  <div class="abs hero-panel"><h1>Local real estate experts<br>lending to local real estate<br>investors</h1></div>
  <svg class="abs hero-curve" width="1200" height="92" viewBox="0 0 1200 92">
    <path d="M0 53 Q240 82 485 86 L600 27 L715 86 Q960 82 1200 53 L1200 92 L0 92 Z" fill="#fff"/>
    <path d="M0 53 Q240 82 485 86 L600 27 L715 86 Q960 82 1200 53" fill="none" stroke="#0b4d2c" stroke-width="4"/>
  </svg>
  <div class="abs hero-dots"><span class="dot active"></span><span class="dot"></span><span class="dot"></span></div>
</section>

<section class="about">
  <h2 class="abs section-title" style="top:882px">About Us</h2>
  <p class="abs about-copy">Lorem Ipsum is simply dummy text of the printing and typesetting industry. Lorem Ipsum has been the industry's standard dummy text ever since the 1500s, when an unknown printer took a galley of type and scrambled it to make a type specimen book. It has survived not only five centuries, but also the leap into electronic typesetting.</p>
  <div class="abs btn" style="left:386px;top:1023px">LEARN MORE</div>
  <div class="abs btn" style="left:605px;top:1023px">APPLY NOW</div>
</section>

<section class="loans">
  <div class="abs loans-band"></div>
  <div class="abs loans-photo" role="img" aria-label="Photo of a hand holding a small house folded from banknotes"></div>
  <h2 class="abs loans-title">Loans <span class="soft">We Provide</span></h2>
  <div class="abs loan" style="top:1240px">
    <span class="loan-mark"></span>
    <h3>Fix And Flop</h3>
    <p>Lorem Ipsum is simply dummy text of the printing and typesetting industry. Lorem Ipsum has been the industry's standard dummy text ever since the 1500s... <span class="more">&raquo;</span></p>
  </div>
  <div class="abs loan" style="top:1391px">
    <span class="loan-mark"></span>
    <h3>Commercial Hard Money Loans</h3>
    <p>Lorem Ipsum is simply dummy text of the printing and typesetting industry. Lorem Ipsum has been the industry's standard dummy text ever since the 1500s... <span class="more">&raquo;</span></p>
  </div>
</section>

<section class="team">
  <h2 class="abs section-title" style="top:1580px">Our <span class="soft">Team</span></h2>
  <div class="abs team-card" style="left:76px"><div class="team-photo" role="img" aria-label="Portrait photo of team member"></div><div class="team-name">Dale Harwin Jr.</div></div>
  <div class="abs team-card" style="left:342px"><div class="team-photo" role="img" aria-label="Portrait photo of team member"></div><div class="team-name">Rob Telmay Jr.</div></div>
  <div class="abs team-card active" style="left:606px"><div class="team-photo" role="img" aria-label="Portrait photo of team member"></div><div class="team-name">Owen Carrick</div></div>
  <div class="abs team-card" style="left:872px"><div class="team-photo" role="img" aria-label="Portrait photo of team member"></div><div class="team-name">Sam Pellow</div></div>
</section>

<section class="blog">
  <div class="abs blog-band"></div>
  <h2 class="abs section-title" style="top:2035px">Blog</h2>
  <article class="abs blog-card" style="left:89px">
    <div class="blog-img" role="img" aria-label="Photo of a businessman holding a tablet" style="background:linear-gradient(135deg,#3c3c3c,#8a8d92 60%,#5a5c60)"></div>
    <div class="blog-date"><b>30</b><span>Nov</span></div>
    <div class="blog-text"><h4>Lorem Ipsum is simply dummy...</h4><p>Lorem Ipsum is simply dummy text of the printing and typesetting.</p></div>
  </article>
  <article class="abs blog-card" style="left:446px">
    <div class="blog-img" role="img" aria-label="Photo of hands reviewing financial charts" style="background:linear-gradient(135deg,#dce6f2,#5f86b8 55%,#24446e)"></div>
    <div class="blog-date"><b>30</b><span>Nov</span></div>
    <div class="blog-text"><h4>Lorem Ipsum is simply dummy ...</h4><p>Lorem Ipsum is simply dummy text of the printing and typesetting.</p></div>
  </article>
  <article class="abs blog-card" style="left:801px">
    <div class="blog-img" role="img" aria-label="Photo of two colleagues working at a laptop" style="background:linear-gradient(135deg,#f1ece6,#c9b8a6 50%,#3b3f46)"></div>
    <div class="blog-date"><b>30</b><span>Nov</span></div>
    <div class="blog-text"><h4>Lorem Ipsum is simply dummy ...</h4><p>Lorem Ipsum is simply dummy text of the printing and typesetting.</p></div>
  </article>
</section>

<footer>
  <h3 class="abs footer-heading" style="left:78px">Contact Info</h3>
  <div class="abs contact-row" style="top:2496px">
    <svg width="16" height="22" viewBox="0 0 16 22"><path fill="#222" d="M8 0a8 8 0 0 0-8 8c0 6 8 14 8 14s8-8 8-14a8 8 0 0 0-8-8zm0 11a3 3 0 1 1 0-6 3 3 0 0 1 0 6z"/></svg>
    <span>street area city, state country.<br>39005</span>
  </div>
  <div class="abs contact-row" style="top:2548px">
    <svg width="16" height="16" viewBox="0 0 24 24"><path fill="#222" d="M6.6 10.8a15.1 15.1 0 0 0 6.6 6.6l2.2-2.2c.3-.3.7-.4 1-.2 1.1.4 2.3.6 3.6.6.6 0 1 .4 1 1V20c0 .6-.4 1-1 1A17 17 0 0 1 3 4c0-.6.4-1 1-1h3.5c.6 0 1 .4 1 1 0 1.3.2 2.5.6 3.6.1.3 0 .7-.2 1z"/></svg>
    <span>123 456 7890</span>
  </div>
  <div class="abs contact-row" style="top:2576px">
    <svg width="18" height="14" viewBox="0 0 18 14"><rect x="1" y="1" width="16" height="12" fill="none" stroke="#222" stroke-width="1.6"/><path d="M1 1l8 7 8-7" fill="none" stroke="#222" stroke-width="1.6"/></svg>
    <span>info@rtv.com.au</span>
  </div>

  <h3 class="abs footer-heading" style="left:435px">News Feed</h3>
  <div class="abs news-item" style="top:2498px">
    <div class="avatar" role="img" aria-label="Author thumbnail"></div>
    <p>Lorem Ipsum is simply dummy text of the printing.<a href="#">Lorem Ipsum</a></p>
  </div>
  <div class="abs news-item" style="top:2573px">
    <div class="avatar" role="img" aria-label="Author thumbnail"></div>
    <p>Lorem Ipsum is simply dummy text of the printing.<a href="#">Lorem Ipsum</a></p>
  </div>

  <h3 class="abs footer-heading" style="left:794px">Newsletter</h3>
  <p class="abs newsletter-copy">Lorem Ipsum is simply dummy text of the printing and typesetting industry. Lorem Ipsum.</p>
  <div class="abs subscribe">
    <span>Enter your Email Id</span>
    <span class="subscribe-btn"><svg width="24" height="24" viewBox="0 0 24 24"><path d="M2 11L22 2l-7 20-3-8z M12 14l10-12" fill="none" stroke="#fff" stroke-width="2" stroke-linejoin="round"/></svg></span>
  </div>

  <div class="abs copyright">© RTV Finance&nbsp; 2017. All Rights Reserved.</div>
</footer>

</body>
</html>
```